Packaging design for a reclosable bag for our product

We have a logo, and we need to put it on packaging for our product and while we want the look to be simple, we want it to follow good design principles and also contain spaces for other product descriptions.

There will be 5 sizes at launch so I'd like 5 variations, one for each size.

I've included a few mockups of the type of bag that I made but they are all just rough ideas that I had.

I want the brand to look scientific and methodical and even a bit quirky, as in "wow this is a serious product but also a bit unusual."

```html
<!DOCTYPE html>
<html lang="en">
<head>
<meta charset="utf-8">
<title>QT4 Bias Lighting – Pouch Options</title>
<link href="https://fonts.googleapis.com/css2?family=Tinos:wght@400;700&family=Poppins:wght@400;600;700&family=Sofia&family=Poiret+One&family=Quicksand:wght@400;500;700&display=swap" rel="stylesheet">
<style>
  :root {
    --canvas: #ececec;
    --ink: #1a1a1a;
    --pouch-dark: #242424;
    --pouch-dark-edge: #151515;
    --pouch-light: #f4f4f4;
    --pouch-light-edge: #dadada;
    --on-dark: #ffffff;
    --on-light: #1a1a1a;
    --muted-dark: #dcdcdc;
    --muted-light: #4a4a4a;
  }
  * { box-sizing: border-box; margin: 0; padding: 0; }
  html, body { width: 1200px; height: 3328px; overflow: hidden; background: var(--canvas); }

  .option-row { position: relative; width: 1200px; height: 832px; }
  .option-label {
    position: absolute; left: 58px; top: 380px;
    transform: translate(-50%, -50%) rotate(-90deg);
    font-family: "Tinos", serif; font-size: 70px; color: var(--ink);
    white-space: nowrap; letter-spacing: 1px;
  }

  .pouch {
    position: absolute; top: 90px; width: 442px; height: 588px;
    display: flex; flex-direction: column; align-items: center;
    padding-top: 158px; text-align: center;
  }
  .pouch--dark { left: 142px; background: linear-gradient(160deg, var(--pouch-dark), var(--pouch-dark-edge)); color: var(--on-dark); }
  .pouch--light { left: 638px; background: linear-gradient(160deg, var(--pouch-light), var(--pouch-light-edge)); color: var(--on-light); }
  .zip-track { position: absolute; top: 78px; left: 18px; right: 18px; height: 3px; background: currentColor; opacity: .12; }

  .brand-name { font-size: 100px; line-height: 100px; letter-spacing: -2px; }
  .product-line { font-size: 27px; margin-top: 6px; letter-spacing: 1px; }
  .size-class { font-size: 17px; margin-top: 38px; }
  .length { font-size: 76px; line-height: 80px; margin-top: 20px; }
  .rule { width: 222px; height: 3px; background: currentColor; margin-top: 4px; }
  .spec { font-size: 18px; line-height: 24px; margin-top: 12px; }
  .pouch--dark .size-class, .pouch--dark .spec { color: var(--muted-dark); }
  .pouch--light .size-class, .pouch--light .spec { color: var(--muted-light); }

  /* Option 1 – classic serif */
  .option-1 .pouch { font-family: "Tinos", serif; }
  .option-1 .brand-name { font-weight: 700; }
  .option-1 .length { font-size: 80px; margin-top: 22px; }

  /* Option 2 – geometric sans */
  .option-2 .pouch { font-family: "Poppins", sans-serif; }
  .option-2 .brand-name { font-weight: 700; }
  .option-2 .product-line { font-weight: 600; font-size: 25px; }
  .option-2 .length { font-weight: 600; }
  .option-2 .pouch--light { padding-top: 126px; }

  /* Option 3 – script accent */
  .option-3 .pouch { font-family: "Poppins", sans-serif; }
  .option-3 .brand-name { font-weight: 700; }
  .option-3 .product-line { font-family: "Sofia", cursive; font-size: 29px; letter-spacing: 2px; }
  .option-3 .length { font-family: "Poiret One", sans-serif; font-size: 80px; }

  /* Option 4 – rounded sans */
  .option-4 .pouch { font-family: "Quicksand", sans-serif; }
  .option-4 .brand-name { font-weight: 700; }
  .option-4 .product-line { font-size: 30px; font-weight: 500; margin-top: 10px; letter-spacing: 0; }
  .option-4 .size-class { font-size: 21px; font-weight: 500; margin-top: 44px; }
  .option-4 .length { font-size: 48px; line-height: 50px; font-weight: 700; margin-top: 2px; }
  .option-4 .spec { margin-top: 30px; }
</style>
</head>
<body>

<section class="option-row option-1">
  <div class="option-label">OPTION-1</div>
  <div class="pouch pouch--dark"><span class="zip-track"></span>
    <div class="brand-name">QT4</div><div class="product-line">BIAS LIGHTING</div>
    <div class="size-class">EXTRA LARGE</div><div class="length">5m</div><div class="rule"></div>
    <div class="spec">6500K White Bias Lighting<br>Simulated D65 CRI 90+</div>
  </div>
  <div class="pouch pouch--light"><span class="zip-track"></span>
    <div class="brand-name">QT4</div><div class="product-line">BIAS LIGHTING</div>
    <div class="size-class">EXTRA LARGE</div><div class="length">5m</div><div class="rule"></div>
    <div class="spec">6500K White Bias Lighting<br>Simulated D65 CRI 90+</div>
  </div>
</section>

<section class="option-row option-2">
  <div class="option-label">OPTION-2</div>
  <div class="pouch pouch--dark"><span class="zip-track"></span>
    <div class="brand-name">QT4</div><div class="product-line">BIAS LIGHTING</div>
    <div class="size-class">EXTRA LARGE</div><div class="length">5m</div><div class="rule"></div>
    <div class="spec">6500K White Bias Lighting<br>Simulated D65 CRI 90+</div>
  </div>
  <div class="pouch pouch--light"><span class="zip-track"></span>
    <div class="brand-name">QT4</div><div class="product-line">BIAS LIGHTING</div>
    <div class="size-class">EXTRA LARGE</div><div class="length">5m</div><div class="rule"></div>
    <div class="spec">6500K White Bias Lighting<br>Simulated D65 CRI 90+</div>
  </div>
</section>

<section class="option-row option-3">
  <div class="option-label">OPTION-3</div>
  <div class="pouch pouch--dark"><span class="zip-track"></span>
    <div class="brand-name">QT4</div><div class="product-line">Bias Lighting</div>
    <div class="size-class">EXTRA LARGE</div><div class="length">5m</div><div class="rule"></div>
    <div class="spec">6500k White Bias Lighting<br>Simulated D65 Cri 90+</div>
  </div>
  <div class="pouch pouch--light"><span class="zip-track"></span>
    <div class="brand-name">QT4</div><div class="product-line">Bias Lighting</div>
    <div class="size-class">EXTRA LARGE</div><div class="length">5m</div><div class="rule"></div>
    <div class="spec">6500k White Bias Lighting<br>Simulated D65 Cri 90+</div>
  </div>
</section>

<section class="option-row option-4">
  <div class="option-label">OPTION-4</div>
  <div class="pouch pouch--dark"><span class="zip-track"></span>
    <div class="brand-name">QT4</div><div class="product-line">Bias Lighting</div>
    <div class="size-class">EXTRA LARGE</div><div class="length">5m</div>
    <div class="spec">6500k White Bias Lighting<br>Simulated D65 Cri 90+</div>
  </div>
  <div class="pouch pouch--light"><span class="zip-track"></span>
    <div class="brand-name">QT4</div><div class="product-line">Bias Lighting</div>
    <div class="size-class">EXTRA LARGE</div><div class="length">5m</div>
    <div class="spec">6500k White Bias Lighting<br>Simulated D65 Cri 90+</div>
  </div>
</section>

</body>
</html>
```